Healthcare and Professional IT Services Company need a redesigned business card

We are a IT Services company that targets small medical practices and professional business such as Attorneys, Accounts, Architects etc. We want to communicate a professional yet friendly image using recent logo redesign here on ArtHarbor. Like to see the colors blue and orange in the design. Must use the Tall Pine Computing as displayed in the new logo - then also want to incorporate the fish logo as well.

Target Market(s)

Small medical and professional services

Industry/Entity Type

It Company

Contact Information for Business Card

The usual stuff, place for name address phone website. Also maybe our tagline which is "Rooted in technology"

Requirements
Must have
• My new logo and the fish somewhere on the card

```html
<!DOCTYPE html>
<html lang="en">
<head>
<meta charset="utf-8">
<title>Tall Pine Computing – Business Card</title>
<link href="https://fonts.googleapis.com/css2?family=Questrial&display=swap" rel="stylesheet">
<style>
  :root {
    --page: #ecebe8;
    --brand-blue: #0a9ade;
    --logo-blue: #1e8fd6;
    --accent-orange: #f39a1e;
    --ink: #5a5a5a;
    --rule: #a9d6f2;
    --card-white: #ffffff;
    --art-light: #d3ebf8;
    --art-dark: #2aa7e6;
  }
  * { box-sizing: border-box; margin: 0; padding: 0; }
  html, body {
    width: 1200px; height: 997px; overflow: hidden;
    background: var(--page);
    font-family: "Questrial", "Century Gothic", sans-serif;
  }
  .sheet { position: relative; width: 1200px; height: 997px; }
  .card {
    position: absolute; left: 280px;
    width: 640px; height: 366px;
    box-shadow: 0 6px 18px rgba(0,0,0,0.12);
    overflow: hidden;
  }
  /* Front */
  .card--front { top: 115px; background: var(--brand-blue); }
  .front-mascot {
    position: absolute; left: 150px; top: 40px;
    width: 350px; height: 220px; border-radius: 40%;
    background: radial-gradient(ellipse at center, var(--art-dark) 0%, var(--brand-blue) 75%);
  }
  .tagline {
    position: absolute; left: 0; right: 0; top: 288px;
    text-align: center; color: var(--card-white);
    font-size: 17px; letter-spacing: 0.5px;
  }
  /* Back */
  .card--back { top: 516px; background: var(--card-white); }
  .brand {
    position: absolute; left: 40px; top: 80px; width: 230px;
    text-align: center;
  }
  .brand-mascot {
    width: 170px; height: 120px; margin: 0 auto 14px;
    border-radius: 40%;
    background: radial-gradient(ellipse at center, var(--art-light) 0%, #eef7fd 80%);
  }
  .brand-name { color: var(--logo-blue); font-size: 26px; line-height: 1.1; }
  .divider {
    position: absolute; left: 300px; top: 60px;
    width: 1px; height: 246px; background: var(--rule);
  }
  .contact { position: absolute; left: 325px; top: 62px; color: var(--ink); }
  .contact-name { color: var(--logo-blue); font-size: 26px; }
  .contact-role { color: var(--accent-orange); font-size: 17px; margin: 2px 0 14px; }
  .contact-address { font-size: 16px; line-height: 1.35; margin-bottom: 14px; }
  .contact-list { list-style: none; font-size: 16px; line-height: 1.7; }
  .contact-list li { display: flex; align-items: center; gap: 10px; }
  .icon { width: 14px; height: 14px; flex: none; }
</style>
</head>
<body>
<main class="sheet">
  <section class="card card--front">
    <div class="front-mascot" role="img" aria-label="White outline fish mascot illustration"></div>
    <p class="tagline">Rooted in technology</p>
  </section>

  <section class="card card--back">
    <div class="brand">
      <div class="brand-mascot" role="img" aria-label="Blue outline fish mascot illustration"></div>
      <p class="brand-name">Tall Pine Computing</p>
    </div>
    <div class="divider"></div>
    <div class="contact">
      <p class="contact-name">Ethan Marlow</p>
      <p class="contact-role">CEO/Founder</p>
      <p class="contact-address">4120 Cedar Hollow Road<br>Juneau, Alaska 99801</p>
      <ul class="contact-list">
        <li>
          <svg class="icon" viewBox="0 0 16 16"><path fill="#1e8fd6" d="M3 1l3 3-1.5 2a9 9 0 0 0 5.5 5.5L12 10l3 3-2 2C7 15 1 9 1 3z"/></svg>
          907 555 0148
        </li>
        <li>
          <svg class="icon" viewBox="0 0 16 16"><rect x="1" y="3" width="14" height="10" rx="1" fill="#1e8fd6"/><path d="M1.5 3.5L8 9l6.5-5.5" stroke="#fff" stroke-width="1.3" fill="none"/></svg>
          hello@tallpine.example
        </li>
        <li>
          <svg class="icon" viewBox="0 0 16 16"><circle cx="8" cy="8" r="7" fill="#1e8fd6"/><path d="M1 8h14M8 1c-3 3-3 11 0 14M8 1c3 3 3 11 0 14" stroke="#fff" stroke-width="1" fill="none"/></svg>
          www.tallpine.example
        </li>
      </ul>
    </div>
  </section>
</main>
</body>
</html>
```